Luxury WordPress Website for CORALBASINS

I need a professional WordPress website for Coral Basins. The site should be modern, visually appealing, and user-friendly, reflecting the brand’s luxury and premium identity. It must include a homepage, product/service pages, contact form, and be responsive on both desktop and mobile devices. The design should allow for easy updates and integration of future content, while maintaining a polished and professional look.

Target Market(s)

swimmingpool & spa

Industry/Entity Type

Swimmingpool

Coding

Coded - Design and coding required

Font styles to use
Other font styles liked:
• HaboroSoft

Requirements
Must have
• Exclusive appearance
Nice to have
• • A logo that subtly incorporates water or pool elements. • A color palette that reflects luxury, elegance, and relaxation. • Clean and modern typography that is easy to read across all media. • Iconography or design elements that convey premium quality. • A versatile design that can be adapted for social media, merchandise, and promotional materials. • Optional: A tagline that emphasizes luxury and high-end pool experiences.

```html
<!DOCTYPE html>
<html lang="en">
<head>
<meta charset="utf-8">
<title>Coral Basins — The Art of Luxury Pool Design</title>
<link href="https://fonts.googleapis.com/css2?family=Aldrich&family=Nunito:wght@400;600;700&display=swap" rel="stylesheet">
<style>
:root{
  --sky:#3b93f5;
  --sky-deep:#1a8bd4;
  --teal:#12a894;
  --teal-frame:#0fb0bd;
  --slate:#2c4b5a;
  --ink:#111;
  --white:#fff;
  --link:#1a8fd6;
}
*{box-sizing:border-box;margin:0;padding:0}
html,body{width:1200px;height:4164px;overflow:hidden}
body{position:relative;background:var(--white);font-family:"Nunito",sans-serif;color:var(--ink)}
.abs{position:absolute}
.btn{position:absolute;display:flex;align-items:center;justify-content:center;background:var(--teal);color:var(--white);border-radius:5px;font-size:15px}
.photo{position:absolute}
/* header */
.nav-blob{left:385px;top:0;width:815px;height:130px}
.brand{left:113px;top:40px;display:flex;align-items:center;gap:10px;color:#4c4fb3;font-weight:700;font-size:22px}
.brand .dot{width:22px;height:22px;border-radius:50%;background:#4c4fb3}
.nav-link{position:absolute;top:38px;color:var(--white);font-size:25px;text-decoration:none}
.hero-title{left:89px;top:198px;font-family:"Aldrich",sans-serif;font-weight:400;font-size:52px;line-height:66px}
.hero-sub{left:89px;top:340px;font-size:29px}
/* intro */
.intro-bg{left:0;top:587px;width:1200px;height:1200px;background:linear-gradient(180deg,#3a95f7 0%,#3d9af5 80%,#e9f4ff 100%)}
.intro-frame{left:76px;top:618px;width:189px;height:388px;background:var(--slate)}
.intro-title{left:472px;top:618px;width:640px;font-weight:400;font-size:32px;line-height:41px}
.intro-text{left:467px;top:716px;width:640px;font-size:14px;line-height:46px}
.why-bg{left:45px;top:1082px;width:1102px;height:705px;background:linear-gradient(180deg,var(--sky-deep),#5aaef4 85%,#e9f4ff);border-radius:30px 30px 0 0}
.why-title{left:0;top:1106px;width:1200px;text-align:center;color:var(--white);font-weight:400;font-size:31px}
.card{position:absolute;background:var(--white);border-radius:10px;overflow:hidden;box-shadow:0 2px 6px rgba(0,0,0,.15)}
.card-title{position:absolute;left:13px;font-size:18px}
.card-more{position:absolute;right:16px;bottom:12px;display:flex;align-items:center;gap:14px;font-size:10px;text-decoration:underline}
.card-more .circle{width:24px;height:24px;border:1.5px solid #333;border-radius:50%;display:flex;align-items:center;justify-content:center;text-decoration:none;font-size:13px}
/* services */
.svc-frame{left:45px;top:1889px;width:422px;height:722px;background:var(--teal-frame)}
.svc-title{position:absolute;font-weight:400;font-size:32px}
.svc-text{position:absolute;font-size:15px;line-height:25px}
.feat{position:absolute;display:flex;align-items:center;gap:10px;font-size:15px;line-height:24px}
/* products */
.products-title{left:45px;top:2670px;font-size:32px;font-weight:400}
.band{left:0;top:2972px;width:1200px;height:1192px;background:linear-gradient(180deg,var(--sky) 0%,#3e97f4 60%,#3a88e0 100%)}
.pcard-back{position:absolute;background:var(--sky-deep);border-radius:14px}
.pcard{position:absolute;background:var(--white);border-radius:12px;padding:18px 16px}
.pcard h3{font-weight:400;font-size:26px;line-height:27px}
.pcard p{margin-top:8px;font-size:12px;line-height:17px;color:var(--link);padding-left:12px}
.pcircle{position:absolute;width:220px;height:220px;border-radius:50%;border:3px solid var(--teal)}
.arrow-btn{position:absolute;top:3163px;width:24px;height:24px;border:1.5px solid #333;border-radius:50%;display:flex;align-items:center;justify-content:center;font-size:13px}
/* contact */
.form{left:23px;top:3250px;width:517px;height:529px;background:var(--white);border-radius:10px}
.field{position:absolute;border:1.5px solid #555;border-radius:4px;font-size:18px;padding:14px 8px}
.contact-title{left:577px;top:3546px;font-weight:400;font-size:34px;line-height:32px;color:#1d2f40}
.contact-text{left:577px;top:3617px;width:520px;font-size:15px;line-height:25px;color:#1d2f40}
/* footer */
.foot-wave{left:0;top:3800px;width:1200px;height:364px}
.foot-brand{left:110px;top:3955px;display:flex;align-items:center;gap:12px;color:var(--white);font-weight:700;font-size:26px}
.foot-brand .dot{width:26px;height:26px;border-radius:50%;background:var(--white)}
.foot-link{position:absolute;top:3961px;color:var(--white);font-size:13px;text-decoration:none}
.sub-input{left:810px;top:3949px;width:192px;height:38px;background:var(--white);border-radius:3px;font-size:12px;color:var(--link);padding:11px 18px}
.sub-btn{left:1012px;top:3949px;width:89px;height:38px;background:var(--white);border-radius:3px;font-size:15px;color:var(--link);display:flex;align-items:center;justify-content:center}
.social{position:absolute;top:4031px;width:32px;height:32px;border-radius:50%;background:var(--white)}
.legal-link{position:absolute;top:4120px;color:var(--white);font-size:12px;text-decoration:none}
.copy{left:105px;top:4128px;color:var(--white);font-size:12px}
</style>
</head>
<body>

<!-- Header -->
<svg class="abs nav-blob" viewBox="0 0 815 130" aria-hidden="true"><path d="M0 0H815V70C760 110 700 125 600 128C420 132 160 128 60 80C18 60 0 30 0 0Z" fill="#1a8fd6"/></svg>
<div class="abs brand"><span class="dot"></span>CORAL BASINS</div>
<nav>
  <a class="nav-link" style="left:548px">Home</a><a class="nav-link" style="left:658px">About</a><a class="nav-link" style="left:770px">Product</a><a class="nav-link" style="left:880px">Services</a><a class="nav-link" style="left:1020px">Contact Us</a>
</nav>

<h1 class="abs hero-title">The Art of Luxury<br>Pool Design</h1>
<div class="abs hero-sub">All You Dreams Come True</div>
<div class="btn" style="left:84px;top:406px;width:134px;height:45px">Contact Us</div>
<div class="abs" style="left:658px;top:320px;width:430px;height:198px;background:var(--teal);border-radius:0 0 0 24px"></div>
<div class="photo" role="img" aria-label="Resort swimming pool with lounge chairs" style="left:676px;top:142px;width:432px;height:356px;background:linear-gradient(180deg,#8fae6a 0%,#7fcbe6 30%,#1fa9e0 100%);border-radius:0 32px 0 0"></div>

<!-- Intro -->
<div class="abs intro-bg"></div>
<div class="abs intro-frame"></div>
<div class="photo" role="img" aria-label="Woman relaxing at a candlelit spa" style="left:102px;top:650px;width:327px;height:332px;background:linear-gradient(135deg,#6b4a30,#d2b59a 60%,#f3e8dc);border-radius:8px"></div>
<h2 class="abs intro-title">Achieve your dreams with our custom, Coral Basins</h2>
<p class="abs intro-text">Imagine an exceptional relaxation and leisure space right in your own backyard. With our unparalleled expertise and commitment to excellence, we create above-ground pools that exceed all expectations. Our exclusive, custom-designed models are crafted to combine style, durability, and innovation, offering a unique and refined experience.</p>
<div class="btn" style="left:472px;top:909px;width:131px;height:42px">Learn More</div>

<div class="abs why-bg"></div>
<h2 class="abs why-title">Why Choose Our Coral Basins ?</h2>

<div class="card" style="left:78px;top:1176px;width:402px;height:553px">
  <div class="photo" role="img" aria-label="Aerial view of pool terrace with loungers" style="left:0;top:0;width:402px;height:449px;background:linear-gradient(180deg,#d9d5c9 0%,#b9e1de 45%,#54c9d2 100%)"></div>
  <div class="card-title" style="top:455px">Superior Quality</div>
  <div class="abs" style="left:13px;top:488px;width:380px;font-size:12px;line-height:24px">Each pool is constructed with high-quality materials, ensuring exceptional durability and strength</div>
</div>
<div class="card" style="left:526px;top:1176px;width:284px;height:263px">
  <div class="photo" role="img" aria-label="Elegant pool with garden" style="left:0;top:0;width:284px;height:184px;background:linear-gradient(180deg,#5c8a48,#4dc3e6 55%,#1e9fd8)"></div>
  <div class="card-title" style="top:194px">Elegant Design</div>
  <div class="card-more">Learn more<span class="circle">›</span></div>
</div>
<div class="card" style="left:820px;top:1176px;width:284px;height:263px">
  <div class="photo" role="img" aria-label="Custom stone-walled pool" style="left:0;top:0;width:284px;height:184px;background:linear-gradient(180deg,#8b8a80,#6aa8a4 55%,#3ab0c8)"></div>
  <div class="card-title" style="top:190px">Custom and Tailor-Made</div>
  <div class="card-more">Learn more<span class="circle">›</span></div>
</div>
<div class="card" style="left:526px;top:1463px;width:284px;height:266px">
  <div class="photo" role="img" aria-label="Pool with ladder by a resort" style="left:0;top:0;width:284px;height:188px;background:linear-gradient(180deg,#7ba35a,#44b8e8 45%,#1c98dc)"></div>
  <div class="card-title" style="top:196px">Easy Installation</div>
  <div class="card-more">Learn more<span class="circle">›</span></div>
</div>
<div class="card" style="left:820px;top:1463px;width:284px;height:266px">
  <div class="photo" role="img" aria-label="Pool surrounded by greenery and umbrellas" style="left:0;top:0;width:284px;height:188px;background:linear-gradient(180deg,#f0b640,#6aa24c 45%,#2aa6c7)"></div>
  <div class="card-title" style="top:196px;left:2px">Constant Innovation</div>
  <div class="card-more">Learn more<span class="circle">›</span></div>
</div>

<!-- Services -->
<div class="abs svc-frame"></div>
<div class="photo" role="img" aria-label="Floating breakfast tray in a pool" style="left:70px;top:1905px;width:436px;height:346px;background:linear-gradient(135deg,#c9e7e7,#8fd1d3 60%,#6bbfc4)"></div>
<div class="photo" role="img" aria-label="Aerial view of a rectangular pool" style="left:70px;top:2251px;width:436px;height:346px;background:radial-gradient(ellipse at center,#3fc6d0 0%,#1a9bb0 45%,#12617a 100%)"></div>

<h2 class="svc-title" style="left:555px;top:1892px">Personalized Services</h2>
<p class="svc-text" style="left:555px;top:1955px;width:565px">We understand that every garden and client is unique. That's why we offer personalized services, from design to installation and after-sales support. Our team of experts is here to answer all your questions and guide you throughout your project</p>
<div class="feat" style="left:547px;top:2070px">
  <svg width="44" height="44" viewBox="0 0 44 44" aria-hidden="true"><circle cx="22" cy="24" r="12" fill="none" stroke="#1a9bd6" stroke-width="3"/><path d="M8 24a14 14 0 0 1 28 0" fill="none" stroke="#1a3a5a" stroke-width="3"/><rect x="5" y="22" width="6" height="10" rx="2" fill="#1a3a5a"/><rect x="33" y="22" width="6" height="10" rx="2" fill="#1a3a5a"/></svg>
  <span>Customer<br>support</span></div>
<div class="feat" style="left:736px;top:2070px">
  <svg width="58" height="48" viewBox="0 0 58 48" aria-hidden="true"><g fill="none" stroke="#1a9bd6" stroke-width="3"><circle cx="29" cy="10" r="5"/><circle cx="10" cy="34" r="5"/><circle cx="29" cy="34" r="5"/><circle cx="48" cy="34" r="5"/><path d="M4 46a6 6 0 0 1 12 0M23 46a6 6 0 0 1 12 0M42 46a6 6 0 0 1 12 0M15 16h28"/></g></svg>
  <span>Our team of<br>experts</span></div>
<div class="feat" style="left:946px;top:2064px">
  <svg width="56" height="58" viewBox="0 0 56 58" aria-hidden="true"><path d="M12 10h36l-6 32H16Z" fill="#1a9bd6"/><text x="22" y="34" fill="#fff" font-size="20" font-family="Nunito">%</text><circle cx="16" cy="50" r="4" fill="none" stroke="#1a9bd6" stroke-width="2.5"/><circle cx="40" cy="50" r="4" fill="none" stroke="#1a9bd6" stroke-width="2.5"/><path d="M2 16h8M4 24h8" stroke="#1a9bd6" stroke-width="2.5"/></svg>
  <span>After-sales<br>support</span></div>
<div class="btn" style="left:545px;top:2135px;width:131px;height:43px">Contact Us</div>

<h2 class="svc-title" style="left:563px;top:2218px">Guaranteed Satisfaction</h2>
<p class="svc-text" style="left:563px;top:2283px;width:580px">Your satisfaction is our top priority. We are committed to providing you with exceptional service and the highest quality products. Join our community of satisfied customers who are already enjoying their custom above-ground pools. 10-Year Warranty!</p>
<div class="feat" style="left:558px;top:2430px">
  <svg width="58" height="58" viewBox="0 0 58 58" aria-hidden="true"><circle cx="29" cy="29" r="25" fill="none" stroke="#12a894" stroke-width="5"/><path d="M17 27h6v14h-6zM25 41V27l6-10c3 0 4 2 3 5l-1 4h8c2 0 3 2 2 4l-3 9c-1 2-2 2-4 2z" fill="#1a8fd6"/></svg>
  <span>The highest quality<br>products</span></div>
<div class="btn" style="left:564px;top:2523px;width:131px;height:43px">Contact Us</div>

<!-- Products -->
<h2 class="abs products-title">Our Product</h2>
<div class="abs band"></div>

<div class="pcard-back" style="left:45px;top:2728px;width:293px;height:404px"></div>
<div class="pcard" style="left:61px;top:2738px;width:300px;height:331px"><h3>Minipools</h3><p>pools are designed to offer exceptional durability while being aesthetically appealing. Available in various sizes and colors</p></div>
<div class="photo pcircle" role="img" aria-label="Round steel hot tub overlooking hills" style="left:118px;top:2898px;background:linear-gradient(180deg,#8fb6d8,#5f8a55 45%,#9a7a6a)"></div>

<div class="pcard-back" style="left:440px;top:2728px;width:293px;height:404px"></div>
<div class="pcard" style="left:458px;top:2738px;width:297px;height:331px"><h3>Spa</h3><p>Warm water at body temperature, whirled by many massage jets, massages and caresses the whole body, relaxes your nerves, activates your muscles, stimulates our circulation. need it.</p></div>
<div class="photo pcircle" role="img" aria-label="Garden spa pool" style="left:513px;top:2898px;background:linear-gradient(180deg,#5b7a48,#7bc3d6 55%,#3fa9cc)"></div>

<div class="pcard-back" style="left:834px;top:2728px;width:293px;height:404px"></div>
<div class="pcard" style="left:852px;top:2738px;width:298px;height:331px"><h3 style="font-size:22px;line-height:25px">Galvanized Steel Pools with Composite Wood Coverings</h3><p>For those who prefer a more natural look, our composite wood pools are an excellent option</p></div>
<div class="photo pcircle" role="img" aria-label="Above-ground framed pool in a garden" style="left:907px;top:2898px;background:linear-gradient(180deg,#5f8a45,#6cc6e6 55%,#9aa0a6)"></div>

<div class="arrow-btn" style="left:1051px">‹</div>
<div class="arrow-btn" style="left:1083px">›</div>

<!-- Contact -->
<form class="abs form" aria-label="Contact form">
  <div class="field" style="left:27px;top:39px;width:228px;height:62px">Last name</div>
  <div class="field" style="left:268px;top:39px;width:230px;height:62px">Last name</div>
  <div class="field" style="left:27px;top:121px;width:471px;height:62px">Email</div>
  <div class="field" style="left:27px;top:207px;width:471px;height:63px;padding-left:16px">Phone</div>
  <div class="field" style="left:27px;top:286px;width:471px;height:127px;padding-top:10px">Message</div>
  <div class="btn" style="left:360px;top:447px;width:138px;height:63px;font-size:24px;border-radius:8px">Send</div>
</form>
<div class="photo" role="img" aria-label="Indoor spa pool with loungers" style="left:577px;top:3289px;width:531px;height:212px;background:linear-gradient(180deg,#6d7074,#2b2f33 55%,#0d1a24)"></div>
<h2 class="abs contact-title">Connect with our team of experts<br>Contact us today</h2>
<p class="abs contact-text">Don't wait any longer to transform your garden into a wellness oasis. Contact us today to discover our range of customizable above-ground pools and get a tailored quote. Dive into a world of infinite possibilities with Coral Basins</p>

<!-- Footer -->
<svg class="abs foot-wave" viewBox="0 0 1200 364" aria-hidden="true"><defs><linearGradient id="fg" x1="0" y1="0" x2="0" y2="1"><stop offset="0" stop-color="#3a86e0"/><stop offset="1" stop-color="#2a63c2"/></linearGradient></defs><path d="M0 40C200 0 380 0 560 30S900 70 1200 20V364H0Z" fill="url(#fg)"/></svg>
<div class="abs foot-brand"><span class="dot"></span>CORAL BASINS</div>
<nav>
  <a class="foot-link" style="left:420px">Home</a><a class="foot-link" style="left:490px">About</a><a class="foot-link" style="left:558px">Services</a><a class="foot-link" style="left:640px">Product</a><a class="foot-link" style="left:720px">Contact</a>
</nav>
<div class="abs sub-input">Enter your email</div>
<div class="abs sub-btn">Subscribe</div>
<span class="social" style="left:888px"></span><span class="social" style="left:924px"></span><span class="social" style="left:968px"></span><span class="social" style="left:1014px"></span><span class="social" style="left:1060px"></span>
<div class="abs copy">© 2025 Coral Basins All Rights Reserved</div>
<nav>
  <a class="legal-link" style="left:382px">Privacy Policy</a><a class="legal-link" style="left:495px">Terms of Use</a><a class="legal-link" style="left:603px">Legal</a><a class="legal-link" style="left:668px">Site Map</a>
</nav>

</body>
</html>
```